Detail Shop Business card design

i need a business card design for my new detailing company called 'Brisk's Polish Works'. i want an all black and white design . simple, direct and to the point. i want the designer to choose a fitting font to match the logothe front should have logo, address, phone and email and the back side should have a slogan and text indicating that we offer services on anything including cars, trucks, motorcycles and RVs. slogan will read "we take pride in your ride"
maybe also very small on the back side the IG icon with Brisks_Polish_Works

phone 208.417.6352
address 3847 E Larkin Ave
Spokane WA 99214
email: BrisksPolish@mailvexo.com

Target Market(s)

all ages , auto enthusiasts

Industry/Entity Type

Automotive

Contact Information for Business Card

the front should have logo, address, phone and email and the back side should have a slogan and text indicating that we offer services on anything including cars, trucks, motorcycles and RVs. slogan will read "we take pride in your ride"

phone 208.417.6352
address 3847 E Larkin Ave
Spokane WA 99214

Colors
000000
ffffff

Requirements
Must have
• bold font and very simple design with good spacing
Nice to have
• anything creative from the designer indicating we service any types of vehicles
Should not have
• any colors ,

```html
<!DOCTYPE html>
<html lang="en">
<head>
<meta charset="utf-8">
<title>Brisk's Polish Works – Business Card</title>
<link rel="stylesheet" href="https://fonts.googleapis.com/css2?family=Roboto:wght@300;400;700&family=Roboto+Condensed:wght@400;700&display=swap">
<style>
  :root{
    --ink:#000000;
    --paper:#ffffff;
    --text-grey:#3a3a3a;
    --backdrop:#2c2c2c;
    --shade:#1a1a1a;
  }
  *{margin:0;padding:0;box-sizing:border-box}
  html,body{width:1200px;height:960px;overflow:hidden;background:var(--backdrop)}
  .card{
    position:absolute;width:600px;height:342px;background:var(--paper);
    font-family:'Roboto',sans-serif;color:var(--ink);overflow:hidden;
  }
  .card--front{left:322px;top:110px}
  .card--back{left:320px;top:493px}

  /* front */
  .brand{
    position:absolute;left:40px;top:60px;width:190px;
    display:flex;align-items:center;gap:10px;
    font-family:'Roboto Condensed',sans-serif;font-weight:700;font-size:24px;line-height:1.05;
    text-transform:uppercase;color:var(--ink);
  }
  .brand__dot{flex:none;width:34px;height:34px;border-radius:50%;background:var(--ink)}
  .name-ribbon{position:absolute;right:0;top:87px;width:214px;height:59px}
  .name-ribbon svg{position:absolute;inset:0}
  .name-ribbon__name{
    position:absolute;right:33px;top:8px;color:var(--paper);
    font-family:'Roboto Condensed',sans-serif;font-weight:700;font-size:22px;letter-spacing:.2px;
  }
  .name-ribbon__role{
    position:absolute;right:33px;top:34px;color:var(--paper);
    font-family:'Roboto Condensed',sans-serif;font-size:15px;
  }
  .contact{position:absolute;right:32px;top:201px;list-style:none}
  .contact li{
    display:flex;justify-content:flex-end;align-items:center;gap:10px;
    height:19px;font-size:14px;font-weight:300;color:var(--text-grey);
  }
  .contact svg{width:14px;height:14px;flex:none}
  .address-band{
    position:absolute;left:0;right:0;top:293px;height:29px;background:var(--ink);
    display:flex;justify-content:flex-end;align-items:center;gap:12px;padding-right:32px;
    color:var(--paper);font-size:14px;
  }
  .address-band svg{width:14px;height:16px}

  /* back */
  .hero-art{
    position:absolute;left:115px;top:92px;width:378px;height:133px;
    background:linear-gradient(180deg,#1c1c1c 0%,#000 70%,#333 100%);
    border-radius:60px 60px 8px 8px;
  }
  .slogan{
    position:absolute;left:0;right:0;top:272px;text-align:center;
    font-weight:700;font-size:17px;letter-spacing:.2px;
  }
  .slogan span{display:inline-block;padding:0 6px 3px;border-bottom:2px solid var(--ink)}
  .services{
    position:absolute;left:0;right:0;top:303px;text-align:center;
    font-weight:700;font-size:10.5px;letter-spacing:.1px;
  }
</style>
</head>
<body>

<section class="card card--front">
  <div class="brand"><span class="brand__dot"></span><span>Brisk's Polish Works</span></div>

  <div class="name-ribbon">
    <svg viewBox="0 0 214 59" width="214" height="59" aria-hidden="true">
      <polygon points="0,0 214,0 214,59 14,59 28,29.5" fill="#000"/>
    </svg>
    <span class="name-ribbon__name">DALE MARSH</span>
    <span class="name-ribbon__role">OWNER</span>
  </div>

  <ul class="contact">
    <li>208.417.6352
      <svg viewBox="0 0 14 14" aria-hidden="true"><path d="M3 1l2.5 0 1 3-1.5 1.2c.8 1.6 2 2.8 3.6 3.6L9.8 7.3l3 1v2.5c0 .7-.6 1.2-1.3 1.2C5.8 12 2 8.2 2 2.5 2 1.6 2.4 1 3 1z" fill="#000"/></svg></li>
    <li>208 553 7184
      <svg viewBox="0 0 14 14" aria-hidden="true"><rect x="3.5" y="0.5" width="7" height="13" rx="1.2" fill="none" stroke="#000" stroke-width="1.4"/><circle cx="7" cy="11.3" r=".8" fill="#000"/></svg></li>
    <li>BrisksPolish@mailvexo.com
      <svg viewBox="0 0 14 14" aria-hidden="true"><rect x="1" y="3" width="12" height="8.5" fill="#000"/><polyline points="1,3 7,8 13,3" fill="none" stroke="#fff" stroke-width="1.2"/></svg></li>
    <li>www.briskspolish.com
      <svg viewBox="0 0 14 14" aria-hidden="true"><circle cx="7" cy="7" r="6" fill="#000"/><path d="M4 4.5c1.5 0 2 1 1.5 2s1 1.5 0 3M9 3c-.5 1.5 1 2 2 2M8.5 10c.5-1 1.5-1 2-.5" stroke="#fff" stroke-width="1.1" fill="none"/></svg></li>
  </ul>

  <div class="address-band">3847 E Larkin Ave, Spokane WA 99214
    <svg viewBox="0 0 14 16" aria-hidden="true"><path d="M7 0.5a5.5 5.5 0 0 1 5.5 5.5C12.5 10 7 15.5 7 15.5S1.5 10 1.5 6A5.5 5.5 0 0 1 7 .5z" fill="#fff"/><circle cx="7" cy="6" r="2" fill="#000"/></svg>
  </div>
</section>

<section class="card card--back">
  <div class="hero-art" role="img" aria-label="Black silhouette illustration of a classic hot rod car on a curved ground shadow"></div>
  <p class="slogan"><span>WE TAKE PRIDE IN YOUR RIDE</span></p>
  <p class="services">CARS●TRUCKS●MOTORCYCLES●RVS AND BOATS</p>
</section>

</body>
</html>
```